Website design for an Italian restaurant in Amsterdam

I need a design for a client of mine. It is for Teatro Lucerna, an Italian restaurant in Amsterdam.
We are going for a clean, modern look but we also need to realise an authentic feel.
The restaurant is located in an old movie theatre, that is where the name Teatro Lucerna comes from.
Industry/Entity Type
Italian Restaurant
Number of Pages Required
1 page
Font styles to use
Sans Serif
Colors
Designer to choose colors to be used in the design.

```html
<!DOCTYPE html>
<html lang="en">
<head>
<meta charset="utf-8">
<title>Teatro Lucerna – Ristorante Italiano</title>
<link href="https://fonts.googleapis.com/css2?family=Noto+Serif:wght@400;700&family=Open+Sans:ital,wght@0,400;0,600;1,400&display=swap" rel="stylesheet">
<style>
:root{
  --wine:#9b2f3c;
  --wine-dark:#7e2230;
  --black:#050505;
  --ink:#222;
  --muted:#8a8a8a;
  --cream:#f8f6f2;
  --light:#f2f2f2;
  --panel:#f4f4f4;
  --white:#fff;
  --serif:"Noto Serif", Georgia, serif;
  --sans:"Open Sans", Arial, sans-serif;
}
*{box-sizing:border-box;margin:0;padding:0}
html,body{width:1200px;height:3186px;overflow:hidden}
body{position:relative;background:var(--white);font-family:var(--sans);color:var(--ink)}
.abs{position:absolute}
.center{text-align:center}

/* header */
.site-header{left:0;top:0;width:1200px;height:119px;background:var(--black);border-bottom:4px solid var(--wine-dark)}
.brand{left:70px;top:38px;width:210px;text-align:center;color:var(--white);font-family:var(--serif)}
.brand .name{font-size:21px;letter-spacing:1px;text-transform:uppercase}
.brand .tag{font-size:10px;color:var(--wine);margin-top:2px;letter-spacing:1px}
.search{left:847px;top:12px;width:52px;height:52px;border-radius:50%;background:var(--wine)}
.search svg{position:absolute;left:16px;top:16px}
.call{left:908px;top:26px;color:var(--white);font-family:var(--serif);font-size:16px;letter-spacing:.5px}
.nav{top:82px;color:var(--white);font-family:var(--serif);font-size:12px;letter-spacing:.5px}

/* hero */
.hero{left:0;top:123px;width:1200px;height:605px;background:radial-gradient(ellipse at 45% 70%,#8a6a52 0%,#4a3327 30%,#22150f 60%,#0d0807 100%)}
.hero-kicker{left:0;top:355px;width:1200px;color:var(--white);font-family:var(--serif);font-size:34px;letter-spacing:1px}
.hero-title{left:0;top:414px;width:1200px;color:var(--white);font-family:var(--serif);font-size:46px;letter-spacing:2px}
.btn{background:var(--wine);color:var(--white);font-family:var(--serif);border-radius:26px;text-align:center;letter-spacing:.5px}
.hero-btn{left:497px;top:493px;width:204px;height:47px;line-height:47px;font-size:16px}

/* welcome */
.welcome{left:0;top:728px;width:597px;height:453px;background:var(--cream)}
.welcome-kicker{left:0;top:808px;width:597px;font-family:var(--serif);font-size:20px;color:#333;letter-spacing:1px}
.welcome-title{left:0;top:840px;width:597px;font-family:var(--serif);font-size:34px;color:var(--wine);letter-spacing:1px}
.welcome-text{left:125px;top:910px;width:347px;font-size:11.5px;line-height:25px;color:#555;text-align:center}
.welcome-btn{left:240px;top:1068px;width:174px;height:47px;line-height:47px;font-size:15px}
.bar-photo{left:597px;top:728px;width:603px;height:453px;background:linear-gradient(160deg,#2a0a45 0%,#7c1fd0 35%,#b44cff 55%,#3d0d66 80%,#15041f 100%)}

/* menu */
.menu-bg{left:0;top:1181px;width:1200px;height:678px;background:radial-gradient(ellipse at 50% 50%,#3a2a20 0%,#1d1410 55%,#0b0807 100%)}
.menu-title{left:0;top:1234px;width:1200px;color:var(--white);font-family:var(--serif);font-size:32px;letter-spacing:1px}
.tab{top:1300px;color:var(--white);font-family:var(--serif);font-size:12px;letter-spacing:.5px}
.tab.active{color:#d2525f}
.menu-card{left:117px;top:1355px;width:966px;height:433px;background:var(--white);border-top:4px solid var(--wine)}
.dish{width:360px}
.dish .name{font-family:var(--serif);font-size:13.5px;color:var(--wine);letter-spacing:.3px}
.dish .desc{font-style:italic;font-size:11.5px;color:#777;margin-top:5px}
.price{font-family:var(--serif);font-weight:700;font-size:17px;color:var(--wine)}

/* features */
.features{left:0;top:1859px;width:1200px;height:452px;background:var(--light)}
.card{top:1922px;width:330px;height:336px;background:var(--white);box-shadow:0 1px 3px rgba(0,0,0,.12);overflow:hidden}
.card .photo{height:206px}
.card h3{font-family:var(--serif);font-weight:400;font-size:17px;color:var(--wine);text-align:center;margin-top:20px}
.card p{font-size:12px;line-height:25px;color:#444;text-align:center;width:230px;margin:6px auto 0}
.card .corner{position:absolute;right:0;bottom:0}

/* booking */
.hours{left:172px;top:2383px;width:295px;height:442px;background:var(--wine)}
.hours-head{left:172px;top:2383px;width:295px;height:123px;background:var(--black)}
.hours-brand{left:172px;top:2440px;width:295px;text-align:center;color:var(--white);font-family:var(--serif)}
.hours-brand .name{font-size:21px;text-transform:uppercase;letter-spacing:1px}
.hours-brand .tag{font-size:10px;color:var(--wine);margin-top:2px}
.hour-row{left:198px;width:260px;color:var(--white);font-family:var(--serif);font-size:13px;letter-spacing:.5px}
.hour-row span{position:absolute;top:0}
.booking{left:467px;top:2383px;width:563px;height:442px;background:var(--panel)}
.booking-kicker{left:467px;top:2418px;width:563px;font-family:var(--serif);font-size:20px;color:#222}
.booking-title{left:467px;top:2450px;width:563px;font-family:var(--serif);font-size:32px;color:var(--wine)}
.field{width:189px;height:45px;background:var(--white);border:1px solid #d8d8d8;font-size:11px;color:#333;padding:0 14px;line-height:43px}
.field svg{position:absolute;right:12px;top:15px}
.book-btn{left:669px;top:2725px;width:151px;height:47px;line-height:47px;font-size:14px}

/* footer */
.site-footer{left:0;top:2889px;width:1200px;height:297px;background:var(--black)}
.foot-brand{left:0;top:2950px;width:1200px;text-align:center;color:var(--white);font-family:var(--serif)}
.foot-brand .name{font-size:21px;text-transform:uppercase;letter-spacing:1px}
.foot-brand .tag{font-size:10px;color:var(--wine);margin-top:2px}
.foot-rule{left:0;top:3020px;width:1200px;height:1px;background:#2a2a2a}
.social{top:3037px;width:60px;height:60px;border:1.5px solid #cfcfcf;border-radius:50%}
.social svg{position:absolute;left:19px;top:21px}
.copyright{left:0;top:3128px;width:1200px;text-align:center;color:var(--white);font-size:11.5px}
</style>
</head>
<body>

<header class="site-header abs">
  <div class="brand abs"><div class="name">Teatro Lucerna</div><div class="tag">Ristorante Italiano</div></div>
  <div class="search abs">
    <svg width="20" height="20" viewBox="0 0 20 20"><circle cx="8" cy="8" r="5.5" fill="none" stroke="#fff" stroke-width="2.4"/><line x1="12" y1="12" x2="17" y2="17" stroke="#fff" stroke-width="2.6" stroke-linecap="round"/></svg>
  </div>
  <div class="call abs">CALL US : &nbsp;(+31) 20 555 0142</div>
  <nav>
    <span class="nav abs" style="left:617px">HOME</span>
    <span class="nav abs" style="left:706px">MENU</span>
    <span class="nav abs" style="left:794px">GROUPMENU</span>
    <span class="nav abs" style="left:922px">RESERVATION</span>
    <span class="nav abs" style="left:1058px">CONTACT</span>
  </nav>
</header>

<section>
  <div class="hero abs" role="img" aria-label="Plated grilled lamb rack with roasted vegetables, dark restaurant setting"></div>
  <div class="hero-kicker abs center">TEATRO LUCERNA</div>
  <h1 class="hero-title abs center" style="font-weight:400">AUTHENTIC &nbsp;ITALIAN CUISINE</h1>
  <div class="btn hero-btn abs">BOOK NOW</div>
</section>

<section>
  <div class="welcome abs"></div>
  <div class="welcome-kicker abs center">WELCOME TO</div>
  <h2 class="welcome-title abs center" style="font-weight:400">TEATRO LUCERNA</h2>
  <p class="welcome-text abs">Sed ut perspiciatis unde omnis iste natus error sit voluptatem accusan-tium doloremque laudantium, totam rem aperiam, eaque ipsa quae ab illo inventore veritatis et quasi architecto beatae vitae dicta sunt explicabo. Nemo enim ipsam voluptatem quia voluptas sit aspernatur aut odit aut dolores eos qui ratione voluptatem sequi nesciunt.</p>
  <div class="btn welcome-btn abs">READ MORE</div>
  <div class="bar-photo abs" role="img" aria-label="Backlit bar shelves with bottles and glasses in purple light"></div>
</section>

<section>
  <div class="menu-bg abs" role="img" aria-label="Dimmed table of Italian dishes"></div>
  <h2 class="menu-title abs center" style="font-weight:400">OUR MENU</h2>
  <span class="tab active abs" style="left:275px">ANTIPASTI</span>
  <span class="tab abs" style="left:378px">LE INSALATE</span>
  <span class="tab abs" style="left:496px">LE PASTE</span>
  <span class="tab abs" style="left:592px">IL PESCE</span>
  <span class="tab abs" style="left:684px">LA CARNE</span>
  <span class="tab abs" style="left:783px">CONTORNI</span>
  <span class="tab abs" style="left:886px">DOLCE</span>
  <div class="menu-card abs"></div>

  <div class="dish abs" style="left:149px;top:1406px"><div class="name">PANE BURRO E TAPANADA</div><div class="desc">Bread, garlicbutter and olivetapenade</div></div>
  <div class="price abs" style="left:520px;top:1416px">€4,50</div>
  <div class="dish abs" style="left:149px;top:1476px"><div class="name">CARPACCIO DI MANZO</div><div class="desc">Thinly sliced tenderloin with a pesto of rocketsalad &amp; parmesan</div></div>
  <div class="price abs" style="left:520px;top:1486px">€13,50</div>
  <div class="dish abs" style="left:149px;top:1546px"><div class="name">CARPACCIO DI TONNO</div><div class="desc">Thinly sliced tuna with red onion, capers and rocketsalad</div></div>
  <div class="price abs" style="left:520px;top:1556px">€4,50</div>
  <div class="dish abs" style="left:149px;top:1616px"><div class="name">VITELLO TONNATO</div><div class="desc">Thinly sliced veal with Piemonte tunasauce and large capers</div></div>
  <div class="price abs" style="left:520px;top:1626px">€13,50</div>
  <div class="dish abs" style="left:149px;top:1697px"><div class="name">ANTIPASTO ITALIANO</div><div class="desc">San Daniële ham, pikante salami, Italiaanse worst, italiaanse</div></div>
  <div class="price abs" style="left:520px;top:1707px">€13,50</div>

  <div class="dish abs" style="left:631px;top:1406px"><div class="name">BRUSCHETTA POMODORO E BASILICO</div><div class="desc">Roasted Italian bread with fresh tomatoes, garlic and basil</div></div>
  <div class="price abs" style="left:1000px;top:1416px">€4,50</div>
  <div class="dish abs" style="left:631px;top:1476px"><div class="name">BRUSCHETTA POMODORO E MOZZARELLA</div><div class="desc">Roasted Italian bread with fresh tomatoes, mozzarella, garlic</div></div>
  <div class="price abs" style="left:1000px;top:1486px">€13,50</div>
  <div class="dish abs" style="left:631px;top:1546px"><div class="name">MELANZANA ALLA PARMIGIANA</div><div class="desc">Eggplant with mozzarella and basil, tomatosauce and Parmesan</div></div>
  <div class="price abs" style="left:1000px;top:1556px">€4,50</div>
  <div class="dish abs" style="left:631px;top:1616px"><div class="name">SAUTÉ DI COZZE E VONGOLE</div><div class="desc">Sauté of vongole and clams in a white winesauce</div></div>
  <div class="price abs" style="left:1000px;top:1626px">€13,50</div>
  <div class="dish abs" style="left:631px;top:1697px"><div class="name">GAMBERI AL FORNO</div><div class="desc">Spicy shrimps from the oven</div></div>
  <div class="price abs" style="left:1000px;top:1707px">€13,50</div>
</section>

<section>
  <div class="features abs"></div>
  <article class="card abs" style="left:85px">
    <div class="photo" role="img" aria-label="Plate of cured ham with tomatoes and greens" style="background:linear-gradient(135deg,#5a2a1e,#b8473a 45%,#e6d7cc 80%)"></div>
    <h3>GROUPMENU</h3>
    <p>We serve groupmenus for reservations for 10 guests or more</p>
    <svg class="corner" width="58" height="58" viewBox="0 0 58 58"><polygon points="58,0 58,58 0,58" fill="var(--wine)"/><circle cx="38" cy="40" r="8" fill="#fff"/><path d="M35 40h6M38.5 37l3 3-3 3" fill="none" stroke="var(--wine)" stroke-width="1.8"/></svg>
  </article>
  <article class="card abs" style="left:435px">
    <div class="photo" role="img" aria-label="Grilled lobster dish with vegetables" style="background:linear-gradient(135deg,#1a1410,#7a2e1c 45%,#c25a2b 70%,#2a2a20)"></div>
    <h3>RESERVATION</h3>
    <p>Tables can be reserved online through our website</p>
    <svg class="corner" width="58" height="58" viewBox="0 0 58 58"><polygon points="58,0 58,58 0,58" fill="var(--wine)"/><circle cx="38" cy="40" r="8" fill="#fff"/><path d="M35 40h6M38.5 37l3 3-3 3" fill="none" stroke="var(--wine)" stroke-width="1.8"/></svg>
  </article>
  <article class="card abs" style="left:786px">
    <div class="photo" role="img" aria-label="Risotto with green asparagus on a white plate" style="background:linear-gradient(135deg,#4a4038,#8a7562 40%,#c9c0b4 75%,#6f8a4a)"></div>
    <h3>OTHER</h3>
    <p>For all your questions you can use our contact form</p>
    <svg class="corner" width="58" height="58" viewBox="0 0 58 58"><polygon points="58,0 58,58 0,58" fill="var(--wine)"/><circle cx="38" cy="40" r="8" fill="#fff"/><path d="M35 40h6M38.5 37l3 3-3 3" fill="none" stroke="var(--wine)" stroke-width="1.8"/></svg>
  </article>
</section>

<section>
  <div class="hours abs"></div>
  <div class="hours-head abs"></div>
  <div class="hours-brand abs"><div class="name">Teatro Lucerna</div><div class="tag">Ristorante Italiano</div></div>
  <div class="hour-row abs" style="top:2537px"><span style="left:0">TUESDAY</span><span style="left:110px">-</span><span style="left:163px">18:00 - 23:00</span></div>
  <div class="hour-row abs" style="top:2575px"><span style="left:0">WEDNESDAY</span><span style="left:110px">-</span><span style="left:163px">18:00 - 23:00</span></div>
  <div class="hour-row abs" style="top:2613px"><span style="left:0">THURSDAY</span><span style="left:110px">-</span><span style="left:163px">18:00 - 23:00</span></div>
  <div class="hour-row abs" style="top:2651px"><span style="left:0">FRIDAY</span><span style="left:110px">-</span><span style="left:163px">18:00 - 23:00</span></div>
  <div class="hour-row abs" style="top:2689px"><span style="left:0">SATURDAY</span><span style="left:110px">-</span><span style="left:163px">18:00 - 23:00</span></div>
  <div class="hour-row abs" style="top:2727px"><span style="left:0">SUNDAY</span><span style="left:110px">-</span><span style="left:163px">CLOSED</span></div>
  <div class="hour-row abs" style="top:2765px"><span style="left:0">MONDAY</span><span style="left:110px">-</span><span style="left:163px">CLOSED</span></div>

  <div class="booking abs"></div>
  <div class="booking-kicker abs center">RESTAURANT</div>
  <h2 class="booking-title abs center" style="font-weight:400">ONLINE BOOKING</h2>
  <div class="field abs" style="left:540px;top:2536px">Name :</div>
  <div class="field abs" style="left:745px;top:2536px">Email :</div>
  <div class="field abs" style="left:540px;top:2591px">Date :
    <svg width="13" height="13" viewBox="0 0 13 13"><rect x="1" y="2" width="11" height="10" fill="none" stroke="#555" stroke-width="1.4"/><line x1="1" y1="5" x2="12" y2="5" stroke="#555" stroke-width="1.4"/><rect x="3" y="7" width="2" height="2" fill="#555"/><rect x="6" y="7" width="2" height="2" fill="#555"/><rect x="9" y="7" width="2" height="2" fill="#555"/></svg></div>
  <div class="field abs" style="left:745px;top:2591px">Time :
    <svg width="13" height="13" viewBox="0 0 13 13"><circle cx="6.5" cy="6.5" r="5.3" fill="none" stroke="#555" stroke-width="1.4"/><path d="M6.5 3.5v3h2.5" fill="none" stroke="#555" stroke-width="1.4"/></svg></div>
  <div class="field abs" style="left:540px;top:2647px">People :
    <svg width="10" height="13" viewBox="0 0 10 13"><polygon points="1,5 9,5 5,10" fill="#444"/></svg></div>
  <div class="field abs" style="left:745px;top:2647px">Phone :</div>
  <div class="btn book-btn abs">BOOK NOW</div>
</section>

<footer>
  <div class="site-footer abs"></div>
  <div class="foot-brand abs"><div class="name">Teatro Lucerna</div><div class="tag">Ristorante Italiano</div></div>
  <div class="foot-rule abs"></div>
  <div class="social abs" style="left:386px" role="img" aria-label="Social network link"></div>
  <div class="social abs" style="left:461px" role="img" aria-label="Social network link"></div>
  <div class="social abs" style="left:533px" role="img" aria-label="Social network link"></div>
  <div class="social abs" style="left:603px" role="img" aria-label="Social network link"></div>
  <div class="social abs" style="left:673px" role="img" aria-label="Social network link"></div>
  <div class="social abs" style="left:745px" role="img" aria-label="Email">
    <svg width="20" height="16" viewBox="0 0 20 16"><rect x="1" y="1" width="18" height="14" rx="2" fill="none" stroke="#fff" stroke-width="1.6"/><path d="M1.5 2.5l8.5 7 8.5-7" fill="none" stroke="#fff" stroke-width="1.6"/></svg>
  </div>
  <div class="copyright abs">© Copyrights 2018 Teatro Lucerna.All Rights Reserved.</div>
</footer>

</body>
</html>
```